Magento e-commerce webdesign

We need a full e-commerce design for a company based in France. The website will sell belts (men / women).
In files, you have our logo. We made a try for a brown visit card, but it's just an idea. The brown color can be used if it looks like leather, warning it MUSN'T look like "brown shit" :)
So you are free with color but never forget we sell belts and it's both for men & women (upmarket). You can make your own colors changes on the logo (only colors).
You'll find 2 wireframes with the home page & the category page. Elements are in french. UPDATED : you have a traduction files, but it would better if you can make it in french.
Photos have to be on a white background.
Carroussel & every pictures of the wireframes area are very importants.
Target Market(s)
Men & women
Fashion peoples
Upmarket
Industry/Entity Type
It Company
Requirements
Must have
- work on the colors
- work on the pictures (carroussel, newsletter, ventes privées, services, category)
- pro & upmarket
Nice to have
- Product detail page
- Texts in french
Should not have
- Shitty brown colors

```html
<!DOCTYPE html>
<html lang="fr">
<head>
<meta charset="utf-8">
<title>Sanglia — Ceintures</title>
<link href="https://fonts.googleapis.com/css2?family=Arimo:wght@400;700&family=Josefin+Sans:wght@400;600&display=swap" rel="stylesheet">
<style>
:root{
  --maroon:#5e1424;
  --maroon-dark:#3f0c18;
  --rose:#b8405a;
  --rose-light:#d7728a;
  --link:#b23a50;
  --ink:#333;
  --muted:#777;
  --line:#ddd;
  --panel:#f3f1f1;
  --bg:#ecebeb;
  --white:#fff;
  --blue:#3b5a94;
  --sky:#5bb5e3;
}
*{box-sizing:border-box;margin:0;padding:0}
html,body{width:742px;height:1200px;overflow:hidden}
body{background:var(--bg);font-family:Arimo,Arial,sans-serif;color:var(--ink);font-size:10px}
.page{position:relative;width:742px;height:1200px;background:var(--white)}
.header{height:100px;position:relative}
.brand{position:absolute;left:22px;top:40px;display:flex;align-items:center;gap:8px}
.brand-dot{width:14px;height:14px;border-radius:50%;background:var(--maroon)}
.brand-name{font-family:"Josefin Sans",Arial,sans-serif;font-weight:600;font-size:36px;color:var(--maroon);letter-spacing:1px}
.cart{position:absolute;right:22px;top:30px;text-align:center;font-size:11px;color:var(--ink)}
.cart svg{vertical-align:middle;margin-right:4px}
.search{position:absolute;right:22px;top:78px;width:150px;height:18px;border:1px solid var(--line);display:flex;justify-content:flex-end;align-items:center;padding-right:4px}
.nav{height:22px;background:linear-gradient(var(--maroon),var(--maroon-dark));display:flex;justify-content:space-between;align-items:center;padding:0 22px;color:var(--white);font-size:11px;font-weight:700}
.nav-main span{margin-right:10px}
.nav-side{font-weight:400;font-size:9px}
.crumb{height:28px;padding:9px 22px;font-size:9px;color:var(--muted)}
.layout{display:flex;gap:10px;padding:0 20px}
.sidebar{width:116px}
.main{width:576px}
.filter{margin-top:20px}
.filter-title{height:22px;background:linear-gradient(var(--rose-light),var(--rose));color:var(--white);text-align:center;font-weight:700;font-size:11px;line-height:22px;border-radius:3px 3px 0 0}
.filter ul{list-style:none;background:var(--panel);padding:6px 10px}
.filter li{font-size:9px;color:var(--link);line-height:17px}
.filter li::before{content:"› ";color:var(--muted)}
.promo{margin-top:40px;height:52px;display:flex;border:1px solid var(--line)}
.promo-photo{width:50px;background:linear-gradient(135deg,#c9c2b8,#8e8377)}
.promo-photo.sale{background:linear-gradient(135deg,#4a90c8,#d33a3a)}
.promo-body{flex:1;padding:3px 5px;font-size:8px;color:var(--muted)}
.promo-body b{display:block;color:var(--maroon);font-size:9px;text-align:right}
.promo-body .more{display:inline-block;margin-top:3px;background:#444;color:#fff;padding:1px 4px;font-size:7px;float:right}
.newsletter{margin-top:8px;background:var(--panel);border:1px solid var(--line)}
.newsletter h3{background:var(--maroon);color:#fff;font-size:9px;padding:3px 6px}
.newsletter .field{margin:5px;height:13px;border:1px solid var(--line);background:#fff;font-size:7px;color:var(--muted);padding:1px 3px}
.newsletter .row{display:flex;justify-content:space-between;align-items:center;margin:0 5px 5px;font-size:7px}
.btn{background:#333;color:#fff;font-size:8px;padding:2px 6px}
.banner{height:150px;margin-top:6px;position:relative;background:linear-gradient(120deg,#e9e4e0,#cbbfb6 50%,#efeae7);border:1px solid var(--line)}
.banner-title{position:absolute;left:0;top:10px;width:100%;height:26px;background:linear-gradient(90deg,rgba(94,20,36,.85),rgba(94,20,36,0));color:#fff;font-family:"Josefin Sans",Arial,sans-serif;font-size:15px;line-height:28px;padding-left:14px;letter-spacing:1px}
.grid{display:grid;grid-template-columns:repeat(3,1fr);gap:24px 22px;margin-top:16px;padding:0 10px}
.card-photo{height:166px;border:1px solid var(--line);background:radial-gradient(circle,#7a5a4a 0,#b9a89c 40%,#fff 72%)}
.card-photo.violet{background:radial-gradient(circle,#5b3d6e 0,#a48db4 40%,#fff 72%)}
.card-photo.black{background:radial-gradient(circle,#2c2c2c 0,#8c8c8c 40%,#fff 72%)}
.card p{font-size:8px;color:var(--muted);line-height:11px;margin:6px 0 4px;height:33px}
.card-foot{display:flex;justify-content:space-between;align-items:center;border-top:1px solid var(--line);padding-top:4px}
.price{font-size:11px;font-weight:700}
.services{display:flex;gap:8px;margin:30px 20px 0;height:66px}
.service{flex:1;border:1px solid var(--line);border-radius:4px;padding:6px 8px;font-size:8px;color:var(--muted);background:linear-gradient(#fff,#f4f4f4)}
.service h4{font-size:9px;color:var(--ink);display:flex;align-items:center;gap:4px;margin-bottom:4px}
.cards{display:flex;gap:4px;margin-top:6px}
.cards span{width:24px;height:15px;border-radius:2px;background:#d8d2cc}
.phone{font-size:10px;color:var(--ink);font-weight:700}
.bottom{display:flex;gap:14px;margin:16px 20px 0}
.blog{width:430px;height:182px;background:var(--panel);border:1px solid var(--line);padding:8px 10px;font-size:9px;line-height:12px;color:var(--muted)}
.blog h3{color:var(--maroon);font-size:12px;margin-bottom:8px}
.blog p{margin-bottom:10px}
.social{flex:1;display:flex;flex-direction:column;gap:8px}
.social-box{height:87px;border-radius:4px;background:linear-gradient(var(--blue),#2c4677);color:#fff;text-align:right;padding:18px 16px;font-size:17px;font-weight:700;line-height:24px}
.social-box.sky{background:linear-gradient(#8fd0f0,var(--sky))}
.footer{position:absolute;left:0;bottom:0;width:742px;height:42px;background:linear-gradient(var(--maroon),var(--maroon-dark));color:#fff;font-size:9px;display:flex;justify-content:space-between;align-items:center;padding:0 22px}
</style>
</head>
<body>
<div class="page">
  <header class="header">
    <div class="brand"><span class="brand-dot"></span><span class="brand-name">Sanglia</span></div>
    <div class="cart"><svg width="14" height="12" viewBox="0 0 14 12"><path d="M0 1h3l2 7h7l2-5H4" fill="none" stroke="#333" stroke-width="1.3"/><circle cx="6" cy="10.5" r="1.2" fill="#333"/><circle cx="11" cy="10.5" r="1.2" fill="#333"/></svg>Panier<br>(vide)</div>
    <div class="search"><svg width="10" height="10" viewBox="0 0 10 10"><circle cx="4" cy="4" r="3" fill="none" stroke="#777"/><path d="M6.5 6.5L9.5 9.5" stroke="#777"/></svg></div>
  </header>
  <nav class="nav">
    <div class="nav-main"><span>Homme</span><span>•</span><span>Femme</span><span>•</span><span>Accessoires</span></div>
    <div class="nav-side">Mon compte &nbsp;|&nbsp; Partenaire</div>
  </nav>
  <div class="crumb">Home › Products</div>
  <div class="layout">
    <aside class="sidebar">
      <div class="filter"><div class="filter-title">PRIX</div>
        <ul><li>0 - 20 euros</li><li>10 - 20 euros</li><li>30 - 50 euros</li><li>50 - 100 euros</li><li>etc</li></ul></div>
      <div class="filter"><div class="filter-title">MATIERE</div>
        <ul><li>Synthétique</li><li>Croute de cuir</li><li>Cuir</li></ul></div>
      <div class="filter"><div class="filter-title">TAILLE</div>
        <ul><li>85 cm</li><li>90 cm</li><li>95 cm</li><li>100 cm</li><li>105 cm</li><li>110 cm</li><li>etc</li></ul></div>
      <div class="promo"><div class="promo-photo" role="img" aria-label="Photo du service client"></div>
        <div class="promo-body"><b>Services</b>Lorem ipsum dolor sit amet<span class="more">Read More</span></div></div>
      <div class="promo" style="margin-top:6px"><div class="promo-photo sale" role="img" aria-label="Visuel soldes ventes privées"></div>
        <div class="promo-body"><b>Vente Privee</b>Lorem ipsum dolor sit amet<span class="more">Read More</span></div></div>
      <div class="newsletter"><h3>Newsletter Sign-up</h3>
        <div class="field">Votre adresse e-mail...</div>
        <div class="row"><span>Désabonner</span><span class="btn">Subscribe</span></div></div>
    </aside>
    <main class="main">
      <div class="banner" role="img" aria-label="Ceintures en cuir présentées sur fond clair">
        <div class="banner-title">TITRE DU RAYON</div>
      </div>
      <div class="grid">
        <div class="card"><div class="card-photo" role="img" aria-label="Ceinture marron"></div><p>Lorem Ipsum is simply dummy text of the printing and typesetting industry.</p><div class="card-foot"><span class="price">$ 420.00</span><span class="btn">Buy Now</span></div></div>
        <div class="card"><div class="card-photo violet" role="img" aria-label="Ceinture violette à boucle ornée"></div><p>Lorem Ipsum is simply dummy text of the printing and typesetting industry.</p><div class="card-foot"><span class="price">$ 420.00</span><span class="btn">Buy Now</span></div></div>
        <div class="card"><div class="card-photo black" role="img" aria-label="Ceinture noire"></div><p>Lorem Ipsum is simply dummy text of the printing and typesetting industry.</p><div class="card-foot"><span class="price">$ 420.00</span><span class="btn">Buy Now</span></div></div>
        <div class="card"><div class="card-photo" role="img" aria-label="Ceinture marron"></div><p>Lorem Ipsum is simply dummy text of the printing and typesetting industry.</p><div class="card-foot"><span class="price">$ 420.00</span><span class="btn">Buy Now</span></div></div>
        <div class="card"><div class="card-photo violet" role="img" aria-label="Ceinture violette à boucle ornée"></div><p>Lorem Ipsum is simply dummy text of the printing and typesetting industry.</p><div class="card-foot"><span class="price">$ 420.00</span><span class="btn">Buy Now</span></div></div>
        <div class="card"><div class="card-photo black" role="img" aria-label="Ceinture noire"></div><p>Lorem Ipsum is simply dummy text of the printing and typesetting industry.</p><div class="card-foot"><span class="price">$ 420.00</span><span class="btn">Buy Now</span></div></div>
      </div>
    </main>
  </div>
  <section class="services">
    <div class="service"><h4><svg width="12" height="10"><rect x="0.5" y="0.5" width="11" height="9" rx="1" fill="none" stroke="#555"/><path d="M0 3h12" stroke="#555" stroke-width="2"/></svg>Payment CB + VirePlus</h4><div class="cards"><span></span><span></span><span></span><span></span></div></div>
    <div class="service"><h4><svg width="14" height="10"><rect x="0" y="1" width="9" height="6" fill="#555"/><path d="M9 3h3l2 2v2H9z" fill="#555"/><circle cx="3" cy="8.5" r="1.5" fill="#555"/><circle cx="11" cy="8.5" r="1.5" fill="#555"/></svg>Livraison</h4>It is a long established fact that a reader will be when looking at its layout.</div>
    <div class="service"><h4><svg width="10" height="10"><path d="M2 0h2l1 3-1.5 1a6 6 0 0 0 2.5 2.5L7 5l3 1v2a2 2 0 0 1-2 2A8 8 0 0 1 0 2a2 2 0 0 1 2-2z" fill="#555"/></svg>Service Client</h4><div class="phone">+33 1 02 03 04 05</div>Contact our Service Center</div>
    <div class="service"><h4><svg width="10" height="10"><path d="M1 5l3 3 5-7" fill="none" stroke="#555" stroke-width="2"/></svg>Garantie</h4>It is a long established fact that a reader will be when looking at its layout.</div>
  </section>
  <section class="bottom">
    <div class="blog"><h3>Derniers articles du blog</h3>
      <p>Lorem Ipsum is simply dummy text of the printing and typesetting industry. Lorem Ipsum has been the industry's standard dummy text ever since the 1500s, when an unknown printer took a galley of type and scrambled it to make a type specimen book.</p>
      <p>It was popularised in the 1960s with the release of printed transfer sheets containing Lorem Ipsum passages, and more recently with desktop publishing software including versions of Lorem Ipsum.</p></div>
    <div class="social">
      <div class="social-box">Communauté<br>5177+ Fans</div>
      <div class="social-box sky">Fil d'actu 500+<br>Followers</div>
    </div>
  </section>
  <footer class="footer"><span>Copyright © 2010 sanglia.fr. All rights reserved</span><span>CGV &nbsp;|&nbsp; FAQ &nbsp;|&nbsp; Plan du Site &nbsp;|&nbsp; Crédits</span></footer>
</div>
</body>
</html>
```